Animal Eye Clinic needs a Business card

We are a new veterinary ophthalmology practice (Ridgeline Pet Vision Care) and we need a business card designed. We only see animal eyes - we are not a regular veterinary clinic. We already have a logo. We are looking for a professional, good looking business card to hand out to our clients. We are looking for something simple but professional and contemporary. Our logo is likely the only picture/graphic that needs to be on the card.
Updates

Contact Information for Business Card

Delia Vossman, BSc, DVM, MSc, DipACVO
Veterinary Ophthalmologist

Phone: 250.418.3927
Email: ridgelinepetvisioncare@mailbox-example.net
Website: ridgelinepetvisioncare-example.net
Address: 1874 Thornbury Rd
Kelowna, BC, V1X 4M9

Colors

Designer to choose colors to be used in the design.

Requirements
Must have
• Our logo (attached)

```html
<!DOCTYPE html>
<html lang="en">
<head>
<meta charset="utf-8">
<title>Ridgeline Pet Vision Care – Business Card</title>
<link rel="stylesheet" href="https://fonts.googleapis.com/css2?family=Roboto+Condensed:wght@400;600;700&display=swap">
<style>
  :root {
    --teal: #1b98a8;
    --teal-dark: #17899a;
    --grey: #767676;
    --white: #ffffff;
    --backdrop: #2b2b2b;
    --text-grey: #5c5c5c;
  }
  * { margin: 0; padding: 0; box-sizing: border-box; }
  html, body {
    width: 1200px; height: 900px; overflow: hidden;
    background: var(--backdrop);
    font-family: "Roboto Condensed", sans-serif;
  }
  .card {
    position: absolute; left: 250px;
    width: 700px; height: 400px;
    overflow: hidden;
  }
  .card-front { top: 35px; background: var(--teal); }
  .card-back { top: 465px; background: var(--white); }

  /* Front */
  .front-mark {
    position: absolute; inset: 0;
    display: flex; align-items: center; justify-content: center; gap: 14px;
  }
  .front-mark .mark-dot {
    width: 46px; height: 46px; border-radius: 50%; background: var(--white);
  }
  .front-mark .mark-name {
    color: var(--white); font-weight: 600; font-size: 26px; letter-spacing: 0.5px;
  }

  /* Back */
  .back-shapes { position: absolute; inset: 0; }
  .back-mark {
    position: absolute; left: 40px; top: 52px;
    display: flex; align-items: center; gap: 14px;
  }
  .back-mark .mark-dot {
    width: 54px; height: 54px; border-radius: 50%; background: var(--teal);
  }
  .back-mark .mark-name {
    color: var(--teal); font-weight: 600; font-size: 28px; letter-spacing: 0.5px;
  }
  .person {
    position: absolute; left: 40px; top: 190px; color: var(--white);
  }
  .person-name { font-size: 30px; font-weight: 700; letter-spacing: 1px; line-height: 1; }
  .person-credentials { font-size: 15px; font-weight: 700; margin-top: 4px; }
  .person-title { font-size: 15px; font-weight: 400; margin-top: 1px; }
  .contacts {
    position: absolute; left: 34px; top: 290px; color: var(--white);
    list-style: none; font-size: 14px; line-height: 24px;
  }
  .contacts li { display: flex; align-items: center; gap: 8px; }
  .contacts svg { width: 16px; height: 16px; flex: none; }
  .address {
    position: absolute; right: 40px; bottom: 30px;
    color: var(--white); text-align: right; font-size: 18px; line-height: 24px;
  }
</style>
</head>
<body>

<section class="card card-front" aria-label="Business card front">
  <div class="front-mark">
    <span class="mark-dot"></span>
    <span class="mark-name">Ridgeline Pet Vision Care</span>
  </div>
</section>

<section class="card card-back" aria-label="Business card back">
  <svg class="back-shapes" viewBox="0 0 700 400" width="700" height="400" aria-hidden="true">
    <rect x="0" y="165" width="700" height="235" fill="var(--teal)"/>
    <polygon points="505,165 700,165 700,400 340,400" fill="var(--grey)"/>
    <line x1="505" y1="165" x2="340" y2="400" stroke="var(--white)" stroke-width="4"/>
  </svg>

  <div class="back-mark">
    <span class="mark-dot"></span>
    <span class="mark-name">Ridgeline Pet Vision Care</span>
  </div>

  <div class="person">
    <h1 class="person-name">DELIA VOSSMAN</h1>
    <p class="person-credentials">BSc, DVM, MSc, DipACVO</p>
    <p class="person-title">Veterinary Ophthalmologist</p>
  </div>

  <ul class="contacts">
    <li>
      <svg viewBox="0 0 16 16" aria-hidden="true"><circle cx="8" cy="8" r="6.5" fill="none" stroke="#fff" stroke-width="1.3"/><path d="M5.6 4.8c.4-.3.8-.2 1 .2l.5 1c.1.3 0 .6-.2.8l-.3.3c.4.9 1.1 1.6 2 2l.3-.3c.2-.2.5-.3.8-.2l1 .5c.4.2.5.6.2 1-.6.8-1.4.9-2.4.4A6.5 6.5 0 0 1 5.2 7.2c-.5-1-.4-1.8.4-2.4z" fill="#fff"/></svg>
      250.418.3927
    </li>
    <li>
      <svg viewBox="0 0 16 16" aria-hidden="true"><rect x="1.5" y="3.5" width="13" height="9" fill="none" stroke="#fff" stroke-width="1.3"/><path d="M1.5 3.5 8 9l6.5-5.5" fill="none" stroke="#fff" stroke-width="1.3"/></svg>
      ridgelinepetvisioncare@mailbox-example.net
    </li>
    <li>
      <svg viewBox="0 0 16 16" aria-hidden="true"><circle cx="8" cy="8" r="6.5" fill="none" stroke="#fff" stroke-width="1.3"/><ellipse cx="8" cy="8" rx="3" ry="6.5" fill="none" stroke="#fff" stroke-width="1.1"/><path d="M1.5 8h13M2.5 5h11M2.5 11h11" stroke="#fff" stroke-width="1.1"/></svg>
      www.ridgelinepetvisioncare-example.net
    </li>
  </ul>

  <address class="address" style="font-style:normal">
    1874 Thornbury Rd<br>
    Kelowna, BC, V1X 4M9
  </address>
</section>

</body>
</html>
```